Stylish business cards for KV7

To create an appealing and professional business card design for a WOMEN Owned Construction Supply Company.
2 sided card. Incorporate brand elements, curvy, colorful, sleek and bright. No solid white background. attached samples of styles added shapes/ribbons. Want something with that WOW that looks awesome, factor. It is a new logo, so feel free to mess with logo colors in the blue and teal factors that can look good with both dark and light background. If you want to try a watermark with just the KV7, without the "Supply" that might look cool to.

Industry/Entity Type

Women owned construction supply company

Contact Information for Business Card

Name, Title, and phone number and email, web page. maybe spot for qr code.

Font styles to use
Sans Serif

Requirements
Nice to have
• would love to see colors, maybe stylish ribbon dividers or some sort of 2 or 3 tone color card that compliments logo.
Should not have
• Please do not have all white background. Do not include Home/reale state/ or building images.

```html
<!DOCTYPE html>
<html lang="en">
<head>
<meta charset="utf-8">
<title>KV7 Supply – Business Cards</title>
<link href="https://fonts.googleapis.com/css2?family=Poppins:wght@400;500;600&display=swap" rel="stylesheet">
<style>
  :root {
    --page-bg: #e2e6e7;
    --navy: #1b3858;
    --charcoal: #222327;
    --teal: #1e95bb;
    --ink: #141417;
    --white: #ffffff;
  }
  * { margin: 0; padding: 0; box-sizing: border-box; }
  html, body {
    width: 1200px; height: 960px; overflow: hidden;
    background: var(--page-bg);
    font-family: "Poppins", sans-serif;
  }
  .card {
    position: absolute; left: 250px;
    width: 701px; height: 400px;
    border-radius: 30px; overflow: hidden;
  }
  .card--front { top: 60px; background: var(--navy); }
  .card--back { top: 500px; background: var(--charcoal); }

  .brand {
    position: absolute; display: flex; align-items: center;
    color: var(--teal); font-weight: 600; white-space: nowrap;
  }
  .brand__dot { background: var(--teal); border-radius: 50%; }
  .card--front .brand {
    left: 0; right: 0; top: 160px; justify-content: center;
    font-size: 62px; gap: 18px;
  }
  .card--front .brand__dot { width: 26px; height: 26px; }
  .card--back .brand {
    left: 27px; top: 72px; font-size: 34px; gap: 10px;
  }
  .card--back .brand__dot { width: 16px; height: 16px; }

  .band { position: absolute; inset: 0; }

  .watermark {
    position: absolute; left: 430px; top: 118px;
    font-size: 150px; font-weight: 600; line-height: 1;
    color: var(--ink); letter-spacing: -2px;
  }

  .person { position: absolute; right: 30px; top: 22px; text-align: right; }
  .person__name { color: var(--teal); font-size: 33px; font-weight: 600; line-height: 1.15; }
  .person__name span { font-weight: 400; }
  .person__title { color: var(--white); font-size: 18px; font-weight: 500; margin-top: 2px; }
  .person-accent {
    position: absolute; right: 0; top: 26px;
    width: 19px; height: 53px; background: var(--teal);
  }

  .address {
    position: absolute; left: 27px; top: 225px;
    color: var(--white); font-size: 19px; line-height: 26px;
  }
  .contact-list {
    position: absolute; left: 27px; top: 298px; list-style: none;
    color: var(--white); font-size: 19.5px; line-height: 26px;
  }
  .contact-list li { display: flex; align-items: center; gap: 12px; }
  .contact-list svg { width: 17px; height: 17px; flex: none; }
</style>
</head>
<body>

<section class="card card--front">
  <div class="brand"><span class="brand__dot"></span>KV7 Supply</div>
</section>

<section class="card card--back">
  <svg class="band" viewBox="0 0 701 400" preserveAspectRatio="none" aria-hidden="true">
    <path d="M0 200 H455 C520 200 560 290 701 288 V400 H0 Z" fill="var(--teal)"/>
  </svg>

  <div class="watermark">KV7</div>

  <div class="brand"><span class="brand__dot"></span>KV7 Supply</div>

  <div class="person">
    <div class="person__name">Marta <span>Kovalova</span></div>
    <div class="person__title">Founder &amp; CEO</div>
  </div>
  <div class="person-accent"></div>

  <p class="address">4180 Meadow Ln. Suite 310<br>Austin, TX 78704</p>

  <ul class="contact-list">
    <li>
      <svg viewBox="0 0 24 24" fill="var(--white)" aria-label="Phone"><path d="M6.6 10.8a15 15 0 0 0 6.6 6.6l2.2-2.2a1 1 0 0 1 1-.25 11.4 11.4 0 0 0 3.6.57 1 1 0 0 1 1 1V20a1 1 0 0 1-1 1A17 17 0 0 1 3 4a1 1 0 0 1 1-1h3.5a1 1 0 0 1 1 1c0 1.25.2 2.45.57 3.57a1 1 0 0 1-.25 1z"/></svg>
      (512) 555-0147
    </li>
    <li>
      <svg viewBox="0 0 24 24" fill="var(--white)" aria-label="Email"><path d="M2 5h20v14H2z M4 7v.4l8 5 8-5V7l-8 5z" fill-rule="evenodd"/></svg>
      info@kv7supply.com
    </li>
    <li>
      <svg viewBox="0 0 24 24" fill="none" stroke="var(--white)" stroke-width="2" aria-label="Website"><circle cx="12" cy="12" r="9"/><path d="M3 12h18M12 3c3 3 3 15 0 18M12 3c-3 3-3 15 0 18"/></svg>
      www.kv7supply.com
    </li>
  </ul>
</section>

</body>
</html>
```